Boutique custom software development company needs new business card

Our nearly 20 year old custom software development company would like to better include the fact that we are now providing Bitcoin services. These new services are B2B include education (how to acquire and securely hold Bitcoin) and integrating Bitcoin payments into existing ecommerce sites or other existing systems. Please keep the card clean and simple. Attached is our current design and some other files. vextorial.com

Target Market(s)

businesses owners interested in long term relationship

Industry/Entity Type

Custom software development and Bitcoin

Contact Information for Business Card

Dale Parker, dale@vextorial.com, vextorial.com, (888) 555-VXTRL

Font styles to use
Other font styles liked:
• monospace

Requirements
Must have
• double-sided
Nice to have
• clean and simple
Should not have
• physical address

```html
<!DOCTYPE html>
<html lang="en">
<head>
<meta charset="utf-8">
<title>Vextorial business card</title>
<link href="https://fonts.googleapis.com/css2?family=Space+Mono:wght@400;700&family=Montserrat:wght@300&display=swap" rel="stylesheet">
<style>
  :root {
    --backdrop: #4a4948;
    --card: #151515;
    --brand-blue: #3e72bd;
    --brand-orange: #ef7a22;
    --ink-light: #f2f2f2;
    --emboss: #1d1d1d;
    --emboss-edge: #2a2a2a;
  }
  * { box-sizing: border-box; margin: 0; padding: 0; }
  html, body {
    width: 1200px; height: 801px; overflow: hidden;
    background: var(--backdrop);
  }
  .sheet {
    width: 1200px; height: 801px;
    display: flex; align-items: center; justify-content: center; gap: 40px;
  }
  .card {
    position: relative;
    width: 540px; height: 309px;
    background: var(--card);
    border-radius: 16px;
    border-bottom: 4px solid var(--brand-blue);
    overflow: hidden;
    font-family: "Space Mono", monospace;
  }

  /* front */
  .brand-square {
    position: absolute; left: 30px; top: 34px;
    width: 104px; height: 104px;
    background: var(--brand-blue);
  }
  .wordmark {
    position: absolute; right: 34px; top: 44px;
    text-align: right;
  }
  .wordmark__name {
    font-family: "Space Mono", monospace;
    font-weight: 700; font-size: 40px; line-height: 1;
    color: var(--brand-blue); letter-spacing: 1px;
  }
  .wordmark__tagline {
    margin-top: 8px;
    font-family: "Montserrat", sans-serif; font-weight: 300;
    font-size: 15px; color: var(--brand-blue);
  }
  .divider {
    position: absolute; left: 230px; right: 34px; top: 178px;
    height: 1px; background: var(--brand-blue);
  }
  .person {
    position: absolute; left: 30px; top: 160px;
  }
  .person__name {
    font-weight: 700; font-size: 22px; line-height: 1.1;
    color: var(--brand-blue);
  }
  .person__title {
    font-size: 12px; color: var(--ink-light); margin-top: 2px;
  }
  .contacts {
    list-style: none; margin-top: 14px;
    font-size: 11.5px; color: var(--ink-light); line-height: 1.6;
  }
  .contacts li { display: flex; align-items: center; gap: 8px; }
  .contacts svg { width: 12px; height: 12px; fill: var(--brand-blue); flex: none; }
  .services {
    position: absolute; right: 34px; top: 200px;
    list-style: none; text-align: right;
    font-size: 11.5px; line-height: 1.6; color: var(--ink-light);
  }
  .services__lead { color: var(--brand-blue); font-weight: 700; }

  /* back */
  .emboss {
    position: absolute; left: 0; right: 0; top: 96px;
    text-align: center;
  }
  .emboss__name {
    font-family: "Space Mono", monospace;
    font-weight: 700; font-size: 64px; line-height: 1;
    color: var(--emboss);
    text-shadow: -1px -1px 0 var(--emboss-edge), 1px 1px 1px #0b0b0b;
  }
  .emboss__tagline {
    margin-top: 14px;
    font-family: "Montserrat", sans-serif; font-weight: 300;
    font-size: 26px; color: var(--emboss);
    text-shadow: -1px -1px 0 var(--emboss-edge), 1px 1px 1px #0b0b0b;
  }
</style>
</head>
<body>
<main class="sheet">

  <section class="card card--front" aria-label="Card front">
    <div class="brand-square"></div>

    <div class="wordmark">
      <div class="wordmark__name">VEXTORIAL</div>
      <div class="wordmark__tagline">developer of custom applications</div>
    </div>

    <div class="divider"></div>

    <div class="person">
      <div class="person__name">Dale Parker</div>
      <div class="person__title">Founding Partner</div>
      <ul class="contacts">
        <li>
          <svg viewBox="0 0 24 24" aria-hidden="true"><path d="M6.6 10.8a15.1 15.1 0 0 0 6.6 6.6l2.2-2.2a1 1 0 0 1 1-.25 11.4 11.4 0 0 0 3.6.57 1 1 0 0 1 1 1V20a1 1 0 0 1-1 1A17 17 0 0 1 3 4a1 1 0 0 1 1-1h3.5a1 1 0 0 1 1 1c0 1.25.2 2.45.57 3.6a1 1 0 0 1-.25 1z"/></svg>
          (888) 555-VXTRL
        </li>
        <li>
          <svg viewBox="0 0 24 24" aria-hidden="true"><path d="M2 5h20v14H2zm2 2v.5l8 5 8-5V7l-8 5z"/></svg>
          dale@vextorial.com
        </li>
        <li>
          <svg viewBox="0 0 24 24" aria-hidden="true"><circle cx="12" cy="12" r="10"/></svg>
          www.vextorial.com
        </li>
      </ul>
    </div>

    <ul class="services">
      <li class="services__lead">Bitcoin services</li>
      <li>Education &amp; secure custody</li>
      <li>Payment integration</li>
    </ul>
  </section>

  <section class="card card--back" aria-label="Card back">
    <div class="emboss">
      <div class="emboss__name">VEXTORIAL</div>
      <div class="emboss__tagline">developer of custom applications</div>
    </div>
  </section>

</main>
</body>
</html>
```